SOLVE Study flyer

I need help designing a flyer for a research study that will include brain imaging in adolescents. The info is in the attached document. The study is called the Sequoia Outlook Lantern Valley Echo (SOLVE) study. Ideally this would be returned as a document that I can edit in the future as we will have several new recruitment phases (different age groups, etc. I also would love to have a logo designed as part of this project, but I recognize that might be a separate design request.

```html
<!DOCTYPE html>
<html lang="en">
<head>
<meta charset="utf-8">
<title>SOLVE Study Flyer</title>
<link rel="stylesheet" href="https://fonts.googleapis.com/css2?family=Oswald:wght@500;600;700&family=Manrope:wght@400;500;600;700;800&display=swap">
<style>
  :root {
    --ink-deep: #2c0f5a;
    --ink-navy: #1d1740;
    --purple: #5c3e95;
    --purple-soft: #c5b4de;
    --lavender: #f1ebf8;
    --lavender-pill: #ece2f8;
    --paper: #f8f5fb;
    --teal: #13878f;
    --teal-soft: #dcf6f8;
    --cyan: #1fc0d3;
    --yellow: #f7d51b;
    --text: #241b33;
  }
  * { margin: 0; padding: 0; box-sizing: border-box; }
  html, body { width: 867px; height: 1200px; overflow: hidden; }
  body {
    position: relative;
    background: var(--paper);
    font-family: "Manrope", sans-serif;
    color: var(--text);
  }
  .hero {
    position: absolute; left: 0; top: 0; width: 867px; height: 400px;
    background: var(--lavender);
  }
  .hero-photo {
    position: absolute; left: 420px; top: 0; width: 447px; height: 400px;
    background: linear-gradient(90deg, rgba(241,235,248,1) 0%, rgba(220,214,224,.85) 22%, #d3cbc6 48%, #c6b9ae 72%, #d9d4d2 100%);
  }
  .wave { position: absolute; left: 0; top: 290px; width: 867px; height: 120px; }
  .headline {
    position: absolute; left: 40px; top: 22px;
    font-family: "Oswald", sans-serif; font-weight: 700;
    font-size: 60px; line-height: 58px; letter-spacing: -0.6px;
    color: var(--ink-deep); text-transform: uppercase; white-space: nowrap;
  }
  .headline .accent { color: var(--teal); }
  .subhead {
    position: absolute; left: 44px; top: 216px;
    font-size: 24px; line-height: 31px; font-weight: 600; color: var(--ink-deep);
  }
  .portrait {
    position: absolute; left: 46px; top: 334px; width: 182px; height: 182px;
    border-radius: 50%;
    background: radial-gradient(circle at 50% 45%, #f0e6fb 0%, #e8dcf7 100%);
  }
  .intro {
    position: absolute; left: 300px; top: 428px; width: 500px;
    text-align: center; font-size: 17.5px; line-height: 26px; font-weight: 500;
  }
  .intro strong { color: var(--purple); font-weight: 700; }
  .panel {
    position: absolute; top: 566px; width: 390px; height: 349px;
    border: 2.5px solid var(--teal); border-radius: 10px; background: #fff;
  }
  .panel--study { left: 26px; }
  .panel--eligible { left: 445px; border-color: var(--purple); }
  .panel-tab {
    position: absolute; top: -19px; height: 44px; border-radius: 6px;
    display: flex; align-items: center; justify-content: center;
    font-family: "Oswald", sans-serif; font-weight: 600; font-size: 19px;
    color: #fff; letter-spacing: 0.1px; text-transform: uppercase; white-space: nowrap;
  }
  .panel--study .panel-tab { left: 28px; width: 287px; background: var(--teal); }
  .panel--eligible .panel-tab { left: 29px; width: 321px; background: var(--purple); }
  .item-icon {
    position: absolute; width: 60px; height: 60px; border-radius: 50%;
    display: flex; align-items: center; justify-content: center;
  }
  .panel--study .item-icon { left: 22px; background: var(--teal-soft); color: var(--teal); }
  .panel--eligible .item-icon { left: 28px; background: var(--lavender-pill); color: var(--purple); }
  .item-text {
    position: absolute; font-size: 15.4px; line-height: 21px; font-weight: 500;
  }
  .panel--study .item-text { left: 102px; width: 255px; }
  .panel--eligible .item-text { left: 114px; width: 240px; }
  .item-text b { font-weight: 700; }
  .cta {
    position: absolute; left: 22px; top: 940px; white-space: nowrap;
    font-size: 31px; font-weight: 600; color: var(--purple); letter-spacing: -0.2px;
  }
  .contact-pill {
    position: absolute; left: 21px; top: 1009px; width: 324px; height: 57px;
    background: var(--lavender-pill); border-radius: 7px;
    display: flex; align-items: center; padding-left: 13px;
    font-family: "Oswald", sans-serif; font-weight: 700; font-size: 34px; line-height: 1;
    color: var(--ink-navy); text-transform: uppercase; letter-spacing: -0.4px;
    white-space: nowrap;
  }
  .contact-pill::after {
    content: ""; position: absolute; right: -12px; top: 16px;
    border-left: 12px solid var(--lavender-pill);
    border-top: 12px solid transparent; border-bottom: 12px solid transparent;
  }
  .mail-icon {
    position: absolute; left: 375px; top: 1016px; width: 45px; height: 45px;
    border-radius: 50%; background: var(--cyan);
    display: flex; align-items: center; justify-content: center;
  }
  .email {
    position: absolute; left: 436px; top: 1012px; white-space: nowrap;
    font-size: 37px; line-height: 50px; font-weight: 700; color: var(--cyan); letter-spacing: -0.2px;
  }
  .reward-bar {
    position: absolute; left: 22px; top: 1089px; width: 822px; height: 93px;
    background: var(--purple); border-radius: 18px;
  }
  .gift {
    position: absolute; left: 74px; top: 13px; width: 67px; height: 67px;
    border-radius: 50%; background: var(--lavender-pill);
    display: flex; align-items: center; justify-content: center;
  }
  .reward-text {
    position: absolute; left: 160px; top: 0; height: 93px;
    display: flex; align-items: center;
    font-size: 44px; font-weight: 600; color: #fff; letter-spacing: -0.3px;
    white-space: nowrap;
  }
  .reward-text .amount { color: var(--cyan); font-weight: 800; font-size: 56px; margin-left: 14px; }
  .burst { position: absolute; top: 18px; width: 48px; height: 58px; }
  .burst--left { left: 12px; }
  .burst--right { left: 762px; transform: scaleX(-1); }
</style>
</head>
<body>
  <header class="hero">
    <div class="hero-photo" role="img" aria-label="Photo of a mother hugging her teenage daughter from behind in a bright room"></div>
    <h1 class="headline">Are you the<br>parent of a<br>child <span class="accent">age 10-17?</span></h1>
    <p class="subhead">Do they worry or overthink<br>negative emotions?</p>
  </header>

  <svg class="wave" viewBox="0 0 867 120" aria-hidden="true">
    <path d="M0,73 C60,28 100,13 138,13 C230,13 320,104 394,104 C480,104 560,51 670,51 C760,51 820,80 867,88 L867,120 L0,120 Z" fill="#c5b4de"/>
    <path d="M0,85 C60,42 100,26 138,26 C230,26 320,114 394,114 C480,114 560,62 670,62 C760,62 820,86 867,92 L867,120 L0,120 Z" fill="#f8f5fb"/>
  </svg>

  <div class="portrait" role="img" aria-label="Illustration of a girl in profile with long dark hair"></div>

  <p class="intro">Northvale University researchers are seeking girls <strong>age 10-17</strong> for a study about brain activity in emotions and decision-making and how they relate to puberty, anxiety and depression.</p>

  <section class="panel panel--study">
    <h2 class="panel-tab">Study participation involves</h2>
    <div class="item-icon" style="top:50px">
      <svg width="32" height="30" viewBox="0 0 32 30" fill="currentColor"><rect x="3" y="5" width="20" height="15" rx="1.5" fill="none" stroke="currentColor" stroke-width="2.4"/><circle cx="11" cy="11" r="2.6"/><path d="M6.5 18c0-3 2-4.5 4.5-4.5s4.5 1.5 4.5 4.5z"/><rect x="0" y="21" width="26" height="3" rx="1"/><rect x="19" y="1" width="12" height="9" rx="1.5"/></svg>
    </div>
    <p class="item-text" style="top:49px"><b>One one-hour interview</b> (online or in-person) where your child will discuss their thoughts</p>
    <div class="item-icon" style="top:129px">
      <svg width="28" height="32" viewBox="0 0 28 32" fill="currentColor"><rect x="2" y="4" width="20" height="26" rx="3"/><rect x="7" y="1" width="10" height="6" rx="2"/><rect x="6" y="12" width="3" height="2" fill="#dcf6f8"/><rect x="11" y="12" width="7" height="2" fill="#dcf6f8"/><rect x="6" y="18" width="3" height="2" fill="#dcf6f8"/><rect x="11" y="18" width="5" height="2" fill="#dcf6f8"/><path d="M17 28l2-5 7-7 3 3-7 7z"/></svg>
    </div>
    <p class="item-text" style="top:138px"><b>Online questionnaires</b> (parent and child)</p>
    <div class="item-icon" style="top:214px">
      <svg width="34" height="26" viewBox="0 0 34 26" fill="currentColor"><path d="M22 2h6a6 6 0 0 1 6 6v10a6 6 0 0 1-6 6h-6z"/><path d="M22 6a7 7 0 0 1 0 14" fill="none" stroke="#dcf6f8" stroke-width="2.4"/><rect x="1" y="10" width="18" height="4" rx="1"/><rect x="3" y="15" width="15" height="3" rx="1"/><circle cx="17" cy="9" r="2.4"/></svg>
    </div>
    <p class="item-text" style="top:211px"><b>One two-hour visit</b> where your child will complete an MRI scan, answer questions about their puberty stage, and have a small hair sample taken to study puberty hormones</p>
  </section>

  <section class="panel panel--eligible">
    <h2 class="panel-tab">Your child may be eligible if they</h2>
    <div class="item-icon" style="top:50px">
      <svg width="30" height="32" viewBox="0 0 30 32" fill="currentColor"><circle cx="15" cy="3" r="2"/><path d="M6 14a9 9 0 0 1 18 0v2H6z"/><rect x="9" y="13" width="12" height="5" rx="2" fill="#ece2f8"/><rect x="4" y="22" width="22" height="3" rx="1"/><rect x="4" y="27" width="3" height="5"/><rect x="10" y="27" width="10" height="3"/><rect x="23" y="27" width="3" height="5"/></svg>
    </div>
    <p class="item-text" style="top:70px"><b>Are age 10-17</b></p>
    <div class="item-icon" style="top:142px">
      <svg width="30" height="32" viewBox="0 0 30 32" fill="currentColor"><path d="M8 12a7 7 0 0 1 14 0v6a7 7 0 0 1-14 0z" fill="none" stroke="currentColor" stroke-width="2.4"/><rect x="3" y="2" width="9" height="4" rx="2"/><circle cx="23" cy="5" r="4"/><path d="M4 32c0-6 4-9 11-9s11 3 11 9z"/></svg>
    </div>
    <p class="item-text" style="top:151px">Tend to <b>worry or overthink</b> negative thoughts</p>
    <div class="item-icon" style="top:237px">
      <svg width="26" height="30" viewBox="0 0 26 30" fill="currentColor"><path d="M13 1l11 4v9c0 8-5 13-11 15C7 27 2 22 2 14V5z"/><path d="M8 15l4 4 6-7" fill="none" stroke="#ece2f8" stroke-width="2.4" stroke-linecap="round" stroke-linejoin="round"/></svg>
    </div>
    <p class="item-text" style="top:235px">Have not been diagnosed with <b>psychosis, learning problems, or autism</b></p>
  </section>

  <p class="cta">Interested in participating? Want more information?</p>

  <div class="contact-pill">Please contact us!</div>
  <div class="mail-icon">
    <svg width="24" height="18" viewBox="0 0 24 18" fill="none" stroke="#fff" stroke-width="2"><rect x="1" y="1" width="22" height="16" rx="2.5"/><path d="M2 3l10 7 10-7"/></svg>
  </div>
  <p class="email">solvestudy@nvu.edu</p>

  <div class="reward-bar">
    <svg class="burst burst--left" viewBox="0 0 50 58" aria-hidden="true"><g fill="var(--yellow)" stroke="#2b1d44" stroke-width="1"><path d="M14 3l30 16-3 5-30-14z"/><path d="M4 26h36v6H4z"/><path d="M10 53l30-15 3 5-30 16z"/></g></svg>
    <div class="gift">
      <svg width="38" height="38" viewBox="0 0 38 38" fill="none" stroke="#5c3e95" stroke-width="3" stroke-linejoin="round"><rect x="4" y="12" width="30" height="8" rx="1"/><rect x="7" y="20" width="24" height="15" rx="1"/><path d="M19 12v23M19 12c-4-8-12-7-10-1M19 12c4-8 12-7 10-1"/></svg>
    </div>
    <p class="reward-text">Compensation up to <span class="amount">$140</span></p>
    <svg class="burst burst--right" viewBox="0 0 50 58" aria-hidden="true"><g fill="var(--yellow)" stroke="#2b1d44" stroke-width="1"><path d="M14 3l30 16-3 5-30-14z"/><path d="M4 26h36v6H4z"/><path d="M10 53l30-15 3 5-30 16z"/></g></svg>
  </div>
</body>
</html>
```